The Velvet Easel Co - Photos to Custom Oil Paintings

We need a website and logo designed and built allowing customers to purchase custom oil paintings. The paintings will come from a customers single photograph or even combination of photos. They will be able to complete a straight forward checkout process, selecting their desired medium (oil or charcoal painting), their desired size, the number of figures in the painting, the type of background required (as per photo or let the artist decide). Which will then automaticaly provide the customer with a price for the purchase. Allowing them to add a photo to the order which they can then submit with the order present in their personal account etc etc etc.
Theres one website in particular that i will be competing with. That is based in the US - http://www.brushmorrow.com
I wish to far exceed the appearence of the already present site.
At the moment i wish to include Coinvale in the payment process. Unless there are some cheaper, more cost efficient ways, please let me know.
The company name is The Velvet Easel Co. Domain has been purchased - www.thevelveteasel.co (via Hostlark - Linux)
I have no great sense of design, but the site must be straight forward, eye catching, engaging and give the customer a sense of high quality. Some kind of flash animation with pictures on the front page scrolling?
For myself, the admin side, ideally must be straight forward to maintain. The ability to update customers accounts with info (they will then be informed there is an update in their account etc)
The ability for automated emails from point of sale (sales orders with generated order numbers) to myself. Again automated emails to the customers once the "status" of their order or other information has been submitted to their account (by myself) or a similar system.
Updates
All,
Please note, the budget is able to increase subject to what additional work is needed. As far as the admin area goes. I am open to suggestions to ensure ease of use and efficiency.
Any questions, comments or ideas are fully welcomed.
Many thanks,
Dan Holloway
Industry/Entity Type
It Company
Logo Text
Logo styles of interest
Pictorial/Combination Logo
Abstract Logo
Wordmark Logo
Lettermark Logo
Look and feel
Each slider illustrates characteristics of the customer's brand and the style your logo design should communicate.

```html
<!DOCTYPE html>
<html lang="en">
<head>
<meta charset="utf-8">
<title>The Velvet Easel Co</title>
<link href="https://fonts.googleapis.com/css2?family=Arimo:ital,wght@0,400;0,700;1,400&family=Questrial&display=swap" rel="stylesheet">
<style>
:root{
  --orange-top:#c9451c;
  --orange-bottom:#b8321a;
  --orange-light:#d9621f;
  --cream:#fbf6ea;
  --panel:#fdf8e8;
  --gold:#b8923f;
  --gold-text:#b58c3a;
  --grey-frame:#e6e3d8;
  --grey-inner:#f5f3ec;
  --heading-grey:#b6ad92;
  --text:#4a4a4a;
  --accent:#c4471c;
  --white:#fff;
}
*{box-sizing:border-box;margin:0;padding:0}
html,body{width:1028px;height:1200px;overflow:hidden}
body{background:var(--cream);font-family:"Arimo",Arial,sans-serif;color:var(--text);position:relative}
.header-band{position:absolute;left:0;top:0;width:1028px;height:238px;background:linear-gradient(180deg,var(--orange-top),var(--orange-bottom))}
.page{position:absolute;left:70px;top:238px;width:896px;height:800px;background:var(--white)}
.abs{position:absolute}
.brand{left:84px;top:56px;display:flex;align-items:center;gap:10px;color:var(--white);font-family:"Arimo",sans-serif;font-weight:400;font-size:24px;line-height:1}
.brand-mark{width:18px;height:18px;background:var(--white)}
.account{left:791px;top:0;width:158px;height:29px;background:var(--white);border-radius:0 0 5px 5px;font-size:13px;color:var(--accent);text-align:center;line-height:28px}
.nav{left:407px;top:51px;display:flex;font-size:13px;color:var(--white)}
.nav a{display:block;height:38px;line-height:38px;padding:0 12px;margin-right:16px;color:inherit;text-decoration:none}
.nav a.active{background:var(--white);color:var(--accent);position:relative}
.nav a.active::after{content:"";position:absolute;left:44px;bottom:-8px;border:8px solid transparent;border-bottom:0;border-top-color:var(--white)}
.welcome{left:86px;top:138px;width:863px;height:280px;background:var(--panel)}
.welcome h1{position:absolute;left:12px;top:14px;font-family:"Questrial",sans-serif;font-weight:400;font-size:25px;color:var(--gold-text)}
.welcome p{position:absolute;left:12px;top:58px;width:290px;font-size:11.3px;line-height:19.3px;letter-spacing:.2px}
.read-more{position:absolute;left:185px;top:234px;width:114px;height:28px;background:#c8bb98;color:var(--white);font-size:13px;line-height:28px;padding-left:10px;clip-path:polygon(0 0,100% 0,85% 100%,0 100%)}
.hero{left:470px;top:147px;width:468px;height:262px;background:linear-gradient(135deg,#d9b63a,#7a8a5a 50%,#a03a22);border:5px solid #d8cfae}
.offer{left:86px;top:419px;width:863px;height:65px;background:var(--gold);color:var(--white);padding:20px 0 0 18px;font-size:16px}
.offer strong{font-weight:400;font-size:22px}
.offer svg{position:absolute;right:20px;top:20px}
.finder{left:86px;top:511px;width:863px;height:196px;background:var(--grey-frame)}
.finder-inner{position:absolute;left:9px;top:9px;width:845px;height:178px;background:var(--grey-inner)}
.finder-tab{position:absolute;left:0;top:0;width:290px;height:33px;background:#d8d2bd;color:var(--white);font-size:16px;line-height:33px;padding-left:15px;clip-path:polygon(0 0,100% 0,90% 100%,0 100%)}
.finder-rule{position:absolute;left:0;top:33px;width:845px;height:2px;background:#cfc7aa}
.arrow{position:absolute;top:85px;font-size:34px;color:#c8bb98}
.thumb{position:absolute;top:41px;width:180px;height:129px;border:2px solid var(--white)}
.col-box{background:var(--grey-inner);border:2px solid #ebe7dc}
.col-box h2{height:31px;background:var(--grey-frame);font-family:"Questrial",sans-serif;font-weight:400;font-size:16px;color:var(--heading-grey);line-height:31px;padding-left:11px}
.features{left:86px;top:727px;width:575px;height:283px}
.features ul{list-style:none;padding:14px 12px 0;font-size:11px;line-height:16.5px}
.features li{margin-bottom:16.5px}
.features em{color:var(--accent)}
.testimonials{left:686px;top:727px;width:263px;height:283px}
.testimonials blockquote{padding:12px 8px 0 8px;font-size:11px;line-height:19.3px}
.testimonials cite{display:block}
.testimonials hr{border:0;border-top:1px dotted #999;margin:6px 8px 0}
.testimonials .more{position:absolute;right:16px;bottom:16px;font-size:11px;font-style:italic;text-decoration:underline}
.footer{left:70px;top:1031px;width:896px;height:159px;background:linear-gradient(180deg,var(--orange-light),var(--orange-bottom));border-radius:0 0 4px 4px;color:var(--white)}
.badge{position:absolute;top:28px;height:56px;border:3px solid rgba(255,255,255,.85);border-radius:28px}
.divider{position:absolute;top:18px;width:2px;height:82px;background:rgba(140,30,10,.4)}
.copy{position:absolute;left:18px;top:124px;font-size:13px}
.footer-nav{position:absolute;right:30px;top:122px;font-size:13px;word-spacing:2px}
.footer-nav span{margin:0 12px;opacity:.7}
</style>
</head>
<body>
<div class="header-band"></div>
<div class="page"></div>

<div class="abs brand"><span class="brand-mark"></span><span>The Velvet Easel Co</span></div>
<div class="abs account">Login &nbsp;|&nbsp; Shopping Cart</div>
<nav class="abs nav">
  <a class="active" href="#">How It Works</a><a href="#">Galleries</a><a href="#">Gift ideas</a><a href="#">FAQ</a><a href="#">Prices</a><a href="#">Contact us</a>
</nav>

<section class="abs welcome">
  <h1>Welcome to the velvet easel</h1>
  <p>Sed ut perspiciatis unde omnis iste natus error sit voluptatem accusantium doloremque laudantium, <em>totam rem aperiam, eaque ipsa quae ab illo inventore veritatis et quasi architecto beatae</em> vitae dicta sunt explicabo. Nemo enim ipsam voluptatem quia voluptas sit aspernatur aut odit aut fugit, sed quia consequuntur magni dolores eos qui ratione voluptatem sequi nesciunt. magni dolores eos qui ratione voluptatem. magni dolores eos qui ratione voluptatem.</p>
  <div class="read-more">Read More &gt;&gt;</div>
</section>
<div class="abs hero" role="img" aria-label="Collage of oil paintings: a child by candlelight and a boy sitting on a tyre"></div>

<div class="abs offer"><strong>SAVE UP TO 45% OFF</strong>- From painting to Portrait or Landscape, enjoy savings on over 20 paintings
  <svg width="28" height="28" viewBox="0 0 28 28"><circle cx="14" cy="14" r="12.5" fill="none" stroke="#fff" stroke-width="2"/><path d="M11 8l7 6-7 6" fill="none" stroke="#fff" stroke-width="2.5"/></svg>
</div>

<section class="abs finder">
  <div class="finder-inner">
    <div class="finder-tab">Let Us find your VELVET EASEL</div>
    <div class="finder-rule"></div>
    <div class="arrow" style="left:10px">«</div>
    <div class="thumb" role="img" aria-label="Painting of a woman reading a letter" style="left:43px;background:linear-gradient(135deg,#3a4a5a,#7a5a3a,#2a2a3a)"></div>
    <div class="thumb" role="img" aria-label="Painting of a child by candlelight" style="left:236px;background:linear-gradient(135deg,#b82a1a,#d84a20,#6a1a10)"></div>
    <div class="thumb" role="img" aria-label="Pet portrait of a boxer dog" style="left:430px;background:linear-gradient(135deg,#b84a3a,#a0603a,#7a3a4a)"></div>
    <div class="thumb" role="img" aria-label="Painting of a couple dancing on a beach with umbrellas" style="left:623px;background:linear-gradient(180deg,#8a9aa8,#c8b890,#d8c8a0)"></div>
    <div class="arrow" style="right:10px">»</div>
  </div>
</section>

<section class="abs col-box features">
  <h2>Let Us Paint Your Life!</h2>
  <ul>
    <li><em>Quality</em> - All our artworks are created by hand by experienced professional portrait artists using top quality paints and materials.</li>
    <li><em>Prices</em> - We ask for only 20% advance payment. Our prices are affordable - oil portraits on canvas from $99 and charcoal portraits from $69 only!</li>
    <li><em>Design</em> - Our portrait painters can combine several photos into 1 portrait painting.</li>
    <li><em>Handpainted</em> - Our artworks are hand painted by real painting artists. They are NOT computer generated. Delivery - Our unique express service makes our portraits a great gift idea for anniversary gifts, birthday gifts, photo gifts or any unique gifts.</li>
    <li><em>Variety</em> - Our artists can handle creation of beautiful pet portraits, family portraits, self portraits and much more. Visit our Galleries section for more!</li>
  </ul>
</section>

<section class="abs col-box testimonials">
  <h2>Testimonials</h2>
  <blockquote>"GREAT pet portraits, perfect right down to every brush stroke. The paintings arrived within 2 days of shipping, I am more than impressed with every aspect. Another happy customer, I will be back for more!!!"<cite><em>Marion, Austin, TX</em></cite></blockquote>
  <hr>
  <blockquote>"GREAT pet portraits, perfect right down to every brush stroke. The paintings arrived within 2 days of shipping!!!"<cite><em>Marion, Austin, TX</em></cite></blockquote>
  <span class="more">read more...</span>
</section>

<footer class="abs footer">
  <div class="badge" style="left:182px;width:124px"></div>
  <div class="divider" style="left:342px"></div>
  <div class="badge" style="left:378px;width:124px;border-radius:6px"></div>
  <div class="divider" style="left:535px"></div>
  <div class="badge" style="left:572px;width:124px;border-radius:6px"></div>
  <div class="copy">THE VELVET EASEL @ 2012</div>
  <div class="footer-nav">How It Works<span>: :</span>Galleries<span>: :</span>Gift ideas<span>: :</span>FAQ<span>: :</span>Prices</div>
</footer>
</body>
</html>
```